Quiet Porch Podcast Cover Graphic

We need a graphic designed for a new podcast called "Quiet Porch." The graphic will be used on multiple podcasting platforms as the lead graphic advertising the podcast. The podcast consists of interviews of individuals sharing their life experiences including challenges, successes, lessons learned, and unexpected turns. The purpose of the podcast is to help listeners and participants learn from the life experiences of everyday neighbors. This podcast has a heavy Christian foundation on the parable of the good samaritan. We believe that through hearing the experiences of everyday neighbors, listeners can be strengthened, nourished, and aided to handle their own life challenges and trials. We would like the final design to be simple and reflective of the purpose and the parable of the good samaritan. The final design needs to have the title of the podcast, "Quiet Porch." We believe the best designs will limit the number of colors to less than 5 and will look good in a monochromatic version as well as a color version. We think the color white should be the main color. The graphic should be square in dimensions. We have considered having two hands grasping each other as if to lift the hand from below, but open to other creative simple takes to convey the lessons from the good samaritan.

```html
<!DOCTYPE html>
<html lang="en">
<head>
<meta charset="utf-8">
<title>Quiet Porch Podcast Cover</title>
<link href="https://fonts.googleapis.com/css2?family=Bebas+Neue&family=Great+Vibes&family=Montserrat:wght@500;700&display=swap" rel="stylesheet">
<style>
  :root {
    --ink-black: #000000;
    --sun-core: #fff4cf;
    --sun-glow: #ffc25a;
    --sky-orange: #ec7a2c;
    --sky-deep: #b9461a;
    --title-yellow: #fcf214;
    --frame-white: #ffffff;
    --label-navy: #12193a;
  }
  html, body {
    margin: 0;
    padding: 0;
    width: 1200px;
    height: 1200px;
    overflow: hidden;
    background: var(--ink-black);
  }
  .cover {
    position: relative;
    width: 1200px;
    height: 1200px;
    background: var(--ink-black);
    overflow: hidden;
  }
  .cover__scene {
    position: absolute;
    left: 0;
    top: 0;
    width: 1200px;
    height: 750px;
    background:
      radial-gradient(ellipse 300px 220px at 600px 270px, var(--sun-core) 0%, rgba(255,210,120,0.85) 35%, rgba(255,170,80,0) 100%),
      radial-gradient(ellipse 760px 440px at 600px 300px, var(--sun-glow) 0%, var(--sky-orange) 45%, var(--sky-deep) 80%, #7a2a10 100%),
      var(--sky-orange);
  }
  .cover__scene::after {
    content: "";
    position: absolute;
    left: 0; right: 0; bottom: 0;
    height: 110px;
    background: linear-gradient(to bottom, rgba(0,0,0,0) 0%, rgba(0,0,0,0.85) 60%, var(--ink-black) 100%);
  }
  .cover__frame {
    position: absolute;
    left: 0;
    top: 0;
  }
  .cover__label {
    position: absolute;
    top: 78px;
    left: 0;
    width: 1200px;
    margin: 0;
    text-align: center;
    font-family: "Montserrat", sans-serif;
    font-weight: 500;
    font-size: 42px;
    letter-spacing: 0.95em;
    text-indent: 0.95em;
    color: var(--label-navy);
    line-height: 48px;
  }
  .cover__title-main {
    position: absolute;
    left: 0;
    top: 723px;
    width: 1200px;
    margin: 0;
    text-align: center;
    font-family: "Bebas Neue", sans-serif;
    font-weight: 400;
    font-size: 385px;
    line-height: 1;
    color: var(--title-yellow);
    letter-spacing: 0.01em;
  }
  .cover__title-script {
    position: absolute;
    left: 0;
    top: 505px;
    width: 1200px;
    margin: 0;
    text-align: center;
    font-family: "Great Vibes", cursive;
    font-size: 250px;
    line-height: 300px;
    color: var(--frame-white);
  }
  .cover__author {
    position: absolute;
    left: 0;
    top: 1063px;
    width: 1200px;
    margin: 0;
    text-align: center;
    font-family: "Montserrat", sans-serif;
    font-weight: 700;
    font-size: 66px;
    line-height: 1;
    color: var(--frame-white);
  }
</style>
</head>
<body>
  <main class="cover">
    <div class="cover__scene" role="img" aria-label="Photograph of a person silhouetted on a grassy hilltop, arms raised toward a bright orange sunrise with rays spreading across the sky"></div>

    <svg class="cover__frame" width="1200" height="1200" viewBox="0 0 1200 1200" aria-hidden="true">
      <g stroke="var(--frame-white)" stroke-width="6" fill="none" stroke-linecap="square">
        <polyline points="318,102 42,102 42,1097 264,1097"/>
        <polyline points="880,102 1158,102 1158,1097 936,1097"/>
      </g>
    </svg>

    <p class="cover__label">PODCAST</p>
    <h1 class="cover__title-main">PORCH</h1>
    <p class="cover__title-script">Quiet</p>
    <p class="cover__author">AUTHOR’S NAME</p>
  </main>
</body>
</html>
```